Business Recognition Design

We need a design for a recognition to be given to business leaders in our community.
The recognition shall be made on a brass plaque on wood panel background (picture attached, please use it as a background), and all drawing must be in vectors and only one color (black).
It should also have a logo on the top and signature on the right bottom.
The text is enclosed in DOC file.
Updates

Reason: just to be able to find the best solution

Reason: None of the suggestion is good enough. Logo in general is too big in comparison with the rest of the plate.

Industry/Entity Type

Business

Requirements
Must have
• - standard Windows font (or possibility to install the same font on Windows), as the name on the recognition shall be printed in the same font
Nice to have
• - some graphic element (in curves) representing achievements in business
- should look great :)

```html
<!DOCTYPE html>
<html lang="en">
<head>
<meta charset="utf-8">
<title>Recognition Plaque</title>
<link rel="stylesheet" href="https://fonts.googleapis.com/css2?family=Baloo+2:wght@700;800&family=Ubuntu:wght@400;500;700&display=swap">
<style>
  :root {
    --wood-dark: #4a2612;
    --wood-mid: #7a4424;
    --wood-light: #95593a;
    --brass-deep: #b98a18;
    --brass-mid: #e2b93a;
    --brass-light: #f7df78;
    --brass-edge: #9c7210;
    --ink: #141008;
    --screw-dark: #6d4c0c;
    --screw-light: #f4d66a;
  }
  html, body {
    margin: 0;
    padding: 0;
    width: 1200px;
    height: 915px;
    overflow: hidden;
    background: #ffffff;
  }
  .plaque {
    position: relative;
    width: 1200px;
    height: 915px;
    background:
      linear-gradient(135deg, var(--wood-light) 0%, var(--wood-mid) 35%, var(--wood-dark) 100%);
    box-shadow: inset 0 0 0 3px var(--wood-dark);
    overflow: hidden;
  }
  .brass-plate {
    position: absolute;
    left: 40px;
    top: 40px;
    width: 1120px;
    height: 834px;
    background:
      repeating-linear-gradient(0deg, rgba(255,255,255,0.05) 0 2px, rgba(0,0,0,0.03) 2px 4px),
      linear-gradient(160deg, var(--brass-deep) 0%, var(--brass-mid) 22%, var(--brass-light) 48%, var(--brass-mid) 72%, var(--brass-deep) 100%);
    box-shadow: 0 0 0 2px var(--brass-edge), 2px 3px 6px rgba(0,0,0,0.45);
  }
  .screw {
    position: absolute;
    width: 30px;
    height: 30px;
    margin: -15px 0 0 -15px;
    border-radius: 50%;
    background: radial-gradient(circle at 38% 35%, var(--screw-light) 0%, var(--brass-mid) 40%, var(--screw-dark) 100%);
    box-shadow: 1px 2px 3px rgba(0,0,0,0.5);
  }
  .logo-mark {
    position: absolute;
    left: 523px;
    top: 101px;
    width: 152px;
    height: 152px;
    border: 1.5px solid var(--ink);
    border-radius: 50%;
    box-sizing: border-box;
    display: flex;
    align-items: center;
    justify-content: center;
    font-family: "Ubuntu", sans-serif;
    font-size: 24px;
    color: var(--ink);
  }
  .text-line {
    position: absolute;
    left: 0;
    width: 1200px;
    text-align: center;
    color: var(--ink);
    margin: 0;
    line-height: 1;
  }
  .heading {
    font-family: "Baloo 2", sans-serif;
    font-weight: 800;
    font-size: 46px;
    letter-spacing: 1px;
  }
  .heading--kicker { top: 280px; }
  .heading--award { top: 344px; }
  .dedication {
    top: 432px;
    font-family: "Ubuntu", sans-serif;
    font-size: 28px;
  }
  .recipient {
    top: 476px;
    font-family: "Ubuntu", sans-serif;
    font-size: 42px;
  }
  .recipient strong {
    font-family: "Baloo 2", sans-serif;
    font-weight: 800;
    font-size: 44px;
  }
  .citation {
    top: 566px;
    font-family: "Ubuntu", sans-serif;
    font-size: 27px;
    line-height: 39px;
  }
  .citation strong { font-weight: 700; }
  .signoff {
    position: absolute;
    top: 752px;
    font-family: "Ubuntu", sans-serif;
    font-size: 26px;
    color: var(--ink);
  }
  .signoff--date { left: 245px; }
  .signoff--date sup { font-size: 15px; }
  .signoff--signatory { left: 788px; }
</style>
</head>
<body>
  <div class="plaque">
    <div class="brass-plate"></div>

    <span class="screw" style="left:87px; top:81px"></span>
    <span class="screw" style="left:1121px; top:81px"></span>
    <span class="screw" style="left:87px; top:834px"></span>
    <span class="screw" style="left:1121px; top:834px"></span>

    <div class="logo-mark">logo</div>

    <h1 class="text-line heading heading--kicker">RECOGNITION</h1>
    <h2 class="text-line heading heading--award">The Best Entrepreneur in 2013</h2>

    <p class="text-line dedication">to</p>
    <p class="text-line recipient">Mr. <strong>Daniel R. Whitfield,</strong> MBA</p>

    <p class="text-line citation">
      Under the leadership of Mr. Daniel R. Whitfield, MBA<br>
      the company <strong>DR-WHITFIELD Ltd</strong> has been selected<br>
      by a City Council as the best company of The City.
    </p>

    <span class="signoff signoff--date">4<sup>th</sup> July, 2013</span>
    <span class="signoff signoff--signatory">City Mayor</span>
  </div>
</body>
</html>
```